International Railway Company Needs a Brochure - KVE Steady & Sure for Railway

We need a brochure for an International Company based in Italy called 'KVE'. We develop innovative instruments used in Railway monitoring for diagnostic and maintenance. Our main product is Track Geometry Measurement System (TGMS) - TGMS measuring the track geometry is composed by two profile measurement instruments (left and right) and one inertial pack. All these instruments are installed on a single rigid rod, mounted on a bogie All our products are based on Laser Triangulation Method.
We appreciate to see designs that use color blue but is not required.
The final design should communicate financial safety and growth. Also The final design should communicate our motto 'Steady & Sure'.
We'll send you our Company Logo, photos and contents. We are open to any suggestions.

Our web site is http://www.kvepralto.example/home.html
Updates

We are launching the contest for KVE new logo. It will be finished in 2/5 days. Thanks for your work.

 

Target Market(s)

Our main customers are International Railway Companies (LUVR-France, HT-Germany, OKP-Italy, ZWN-Switzerland) but also private companies.
Please see our competitors brochure in file attached "PXC Track Measuring Systems_EN_v6.pdf"

Industry/Entity Type

Financial

Requirements
Must have
• The brochure must have 6 pages A4 format like the example file PXC Track Measuring Systems_EN_v6

Page 1: Cover Page - KVE Synthesis
Page 2: Synthesis of the following products with one image for each

TMS
TGMS
RPMS
TRMS
TVS
DV

Page 3: TGMS details
Page 4: TMS and RPMS details
Page 5: TRMS and TVS and DV details
Page 6: Contacts

The text is not important. We can add it in a second time.

The file 115643_2387209_226909_vector is Company Logo file.
The file Final_KVE source logo1-bw is "family" Product logo.

Please feel free to change color at both logo if you need to do it or make it trasparent.
Should not have
• In the final brochure we don't want to see our VAT/TVA/IVA

```html
<!DOCTYPE html>
<html lang="en">
<head>
<meta charset="utf-8">
<title>KVE Brochure Covers</title>
<link rel="stylesheet" href="https://fonts.googleapis.com/css2?family=Questrial&display=swap">
<style>
  :root {
    --stage: #e9e7e4;
    --orange: #d9541f;
    --orange-light: #ef7a45;
    --orange-deep: #b8431a;
    --white: #ffffff;
    --band: #f1f1f1;
    --photo-dark: #1e1e1e;
    --photo-mid: #6a6a6a;
    --photo-light: #b9b9b9;
  }
  * { margin: 0; padding: 0; box-sizing: border-box; }
  html, body {
    width: 1200px; height: 1000px; overflow: hidden;
    background: var(--stage);
    font-family: "Questrial", sans-serif;
  }
  .spread {
    position: absolute; top: 165px; left: 110px;
    display: flex; gap: 60px;
  }
  .page {
    position: relative; width: 460px; height: 650px; overflow: hidden;
    box-shadow: 0 6px 24px rgba(0,0,0,0.18);
  }

  .brand-name {
    color: var(--white); font-size: 30px; letter-spacing: 4px; line-height: 1;
  }
  .brand-tagline {
    margin-top: 8px; font-size: 9px; letter-spacing: 3px; text-transform: uppercase;
  }
  .web { letter-spacing: 1px; white-space: nowrap; }
  .web strong { font-weight: 700; }

  /* Back cover */
  .back-cover {
    background: radial-gradient(ellipse at 45% 15%, var(--orange-light) 0%, var(--orange) 55%, var(--orange-deep) 100%);
  }
  .back-cover .brand {
    position: absolute; top: 375px; right: 70px; text-align: center;
  }
  .back-cover .brand-tagline { color: var(--white); }
  .contact-band {
    position: absolute; left: 0; right: 0; top: 458px; height: 110px;
    background: var(--band);
    padding: 20px 28px 0 0; text-align: right;
    font-style: normal;
    color: var(--orange); font-size: 11px; line-height: 1.5;
  }
  .back-cover .web {
    position: absolute; right: 28px; top: 588px;
    color: var(--white); font-size: 16px;
  }

  /* Front cover */
  .front-cover {
    background: linear-gradient(160deg, var(--photo-dark) 0%, var(--photo-mid) 40%, var(--photo-light) 55%, var(--photo-mid) 75%, var(--photo-dark) 100%);
  }
  .cover-photo { position: absolute; inset: 0; }
  .front-cover .brand {
    position: absolute; top: 200px; left: 0; right: 0; text-align: center;
  }
  .front-cover .brand-tagline { color: var(--orange-light); font-size: 10px; }
  .web-tab {
    position: absolute; bottom: 0; left: 150px; width: 290px; height: 42px;
    background: var(--orange); border-radius: 14px 14px 0 0;
    color: var(--white); font-size: 15px;
    display: flex; align-items: center; justify-content: center;
  }
</style>
</head>
<body>
  <main class="spread">
    <section class="page back-cover">
      <div class="brand">
        <div class="brand-name">KVE</div>
        <div class="brand-tagline">Steady &amp; Sure</div>
      </div>
      <address class="contact-band">
        KVE S.r.l. Headquarters Via Lentisco 12<br>
        10100 Almaro - AL ITALY<br>
        Tel: +39 000 5550142<br>
        Fax: +39 000 5550143<br>
        Email: info@kvepralto.example
      </address>
      <div class="web">www.<strong>kve</strong>pralto.example</div>
    </section>

    <section class="page front-cover">
      <div class="cover-photo" role="img" aria-label="Black and white photograph of railway tracks curving into the distance on an elevated line"></div>
      <div class="brand">
        <div class="brand-name">KVE</div>
        <div class="brand-tagline">Steady &amp; Sure</div>
      </div>
      <div class="web-tab web">www.<strong>kve</strong>pralto.example</div>
    </section>
  </main>
</body>
</html>
```